verdant terraces simple classy business card design

my name is colin barrow and I run a gardening business aimed at high class verdant terraces. the business name is verdant terraces and our logo was designed on pixel harbour .My clientel are anything from residential homes to businesses. I take pride in my work and know that I offer a service like no other in my area.
The business card will be used to represent my business and I want it to be not only rememberable, but simplistic and modern. Eye catching too. Of course I would like it relatable to gardening and appealing to the correct clientel - those being garden enthusiasts, prestigious homes and businesses that are after top of the line gardening services like no other on the market.
I am not a typical lawn mowing business so I don't want a typical card design that represents that. The gardens I work with are generally million dollar properties with owners who are very garden proud looking for upkeep and guidance from me along with sometimes whole new garden designs. I want the business cards to show to my clients that I take pride, as they do, in their garden. And I want them to know from my card that I am a professional, qualified horticulturist offering them a top of the line service for life. I want them to refer my business on. I want them to look at my business card and see class and professionalism in a modern unique bold way.
The card should be simple with the possibility of the logo on the front being embossed/debossed and my details on the back the card should have a organic garden feel it's very important to me that it is absolutely perfect
I am also very open to ideas and suggestions so look forward to seeing the designs. the business logo has been supplied with this project and I want the card to be double sided

Contact info is
Colin Barrow - Managing Director / Horticulturist
Phone : 0481 526 704
Email: colinbarrow@verdantterraces.example.au

Target Market(s)

high class gardens residential and commercial

Industry/Entity Type

Gardener

Contact Information for Business Card

Contact info is
Phone : 0481 526 704

PLEASE MAKE CARD DOUBLE SIDED

Requirements
Must have
• organic simple classy modern feel
• must flow with the current logo that has been supplied with this project
• Double sided
• Must explain in a simple way that I deal with high end gardens and I'm a qualified horticulturist
Nice to have
• embossed debossed logo
Should not have
• shouldn't be to busy or cheap looking

```html
<!DOCTYPE html>
<html lang="en">
<head>
<meta charset="utf-8">
<title>Verdant Terraces – Business Card</title>
<link rel="stylesheet" href="https://fonts.googleapis.com/css2?family=Open+Sans:wght@400;600;700&display=swap">
<style>
  :root {
    --canvas: #e9ebee;
    --charcoal: #2b2c2e;
    --charcoal-light: #3a3b3d;
    --leaf: #8cc63f;
    --leaf-light: #a4d65e;
    --fern: #5aab47;
    --brand: #5fae4a;
    --paper: #f6f6f3;
    --ink-light: #ffffff;
    --ink-soft: #e3e3e3;
  }
  * { box-sizing: border-box; margin: 0; padding: 0; }
  html, body {
    width: 1200px; height: 800px; overflow: hidden;
    background: var(--canvas);
    font-family: "Open Sans", "Segoe UI", sans-serif;
  }
  .canvas {
    position: relative; width: 1200px; height: 800px;
    display: flex; flex-direction: column; align-items: center; justify-content: center; gap: 34px;
  }
  .card {
    position: relative; width: 600px; height: 343px;
    border-radius: 4px; overflow: hidden;
    box-shadow: 0 10px 26px rgba(0,0,0,.18);
  }
  .card-art { position: absolute; inset: 0; width: 100%; height: 100%; display: block; }

  /* Brand lockup */
  .brand { position: absolute; display: flex; align-items: center; gap: 12px; }
  .brand-dot { width: 34px; height: 34px; border-radius: 50%; background: var(--brand); flex: none; }
  .brand-name {
    color: var(--brand); font-weight: 600; text-transform: uppercase;
    font-size: 21px; letter-spacing: 3px; line-height: 1.05; white-space: nowrap;
  }
  .brand-line { display: block; }

  /* Details side */
  .card--details .brand { left: 400px; top: 142px; }
  .card--details .brand-name { font-size: 20px; letter-spacing: 2.5px; }
  .contact { position: absolute; left: 22px; top: 46px; list-style: none; }
  .contact-row { display: flex; align-items: flex-start; gap: 12px; margin-bottom: 12px; }
  .contact-icon {
    width: 26px; height: 26px; border-radius: 50%; background: var(--fern);
    display: flex; align-items: center; justify-content: center; flex: none;
  }
  .contact-icon svg { width: 15px; height: 15px; }
  .contact-text { color: var(--ink-soft); font-size: 11px; line-height: 1.35; padding-top: 4px; white-space: nowrap; }
  .contact-name { color: var(--ink-light); font-weight: 700; font-size: 13px; text-transform: uppercase; letter-spacing: .3px; }
  .contact-role { display: block; font-size: 10.5px; }

  /* Logo side */
  .card--logo .brand { left: 50%; top: 108px; transform: translateX(-50%); }
</style>
</head>
<body>
<main class="canvas">

  <!-- Details side -->
  <section class="card card--details" aria-label="Card back with contact details">
    <svg class="card-art" viewBox="0 0 600 343" aria-hidden="true">
      <rect width="600" height="343" fill="var(--paper)"/>
      <path d="M0 0 H432 C382 90 352 210 344 343 H0 Z" fill="var(--leaf-light)"/>
      <path d="M0 0 H408 C358 90 328 210 320 343 H0 Z" fill="var(--fern)"/>
      <path d="M0 0 H384 C334 90 304 210 296 343 H0 Z" fill="var(--leaf)"/>
      <path d="M0 0 H372 C322 90 292 210 284 343 H0 Z" fill="var(--charcoal)"/>
      <path d="M566 228 H600 V272 H566 A22 22 0 0 1 566 228 Z" fill="var(--leaf)"/>
    </svg>

    <ul class="contact">
      <li class="contact-row">
        <span class="contact-icon">
          <svg viewBox="0 0 16 16"><circle cx="8" cy="5" r="3" fill="#fff"/><path d="M2 15 C2 10 14 10 14 15 Z" fill="#fff"/></svg>
        </span>
        <span class="contact-text"><span class="contact-name">Colin Barrow</span><span class="contact-role">Managing Director / Horticulturist</span></span>
      </li>
      <li class="contact-row">
        <span class="contact-icon">
          <svg viewBox="0 0 16 16"><path d="M3 2 L6 2 L7 5 L5 6.5 C6 9 7 10 9.5 11 L11 9 L14 10 L14 13 C8 14 2 8 3 2 Z" fill="#fff"/></svg>
        </span>
        <span class="contact-text">0481 526 704</span>
      </li>
      <li class="contact-row">
        <span class="contact-icon">
          <svg viewBox="0 0 16 16" fill="none" stroke="#fff" stroke-width="1.3"><circle cx="8" cy="8" r="6"/><ellipse cx="8" cy="8" rx="2.6" ry="6"/><path d="M2 8 H14 M3 5 H13 M3 11 H13"/></svg>
        </span>
        <span class="contact-text">colinbarrow@verdantterraces.example.au</span>
      </li>
    </ul>

    <div class="brand">
      <span class="brand-dot"></span>
      <span class="brand-name"><span class="brand-line">Verdant</span><span class="brand-line">Terraces</span></span>
    </div>
  </section>

  <!-- Logo side -->
  <section class="card card--logo" aria-label="Card front with business name">
    <svg class="card-art" viewBox="0 0 600 343" aria-hidden="true">
      <defs>
        <linearGradient id="charcoalFade" x1="0" y1="0" x2="0" y2="1">
          <stop offset="0" stop-color="var(--charcoal-light)"/>
          <stop offset="1" stop-color="var(--charcoal)"/>
        </linearGradient>
      </defs>
      <rect width="600" height="343" fill="url(#charcoalFade)"/>
      <path d="M330 0 H600 V58 C520 40 440 30 380 30 C360 20 345 10 330 0 Z" fill="var(--leaf-light)"/>
      <path d="M0 150 C120 250 360 270 600 200 V343 H0 Z" fill="var(--fern)"/>
      <path d="M0 170 C120 268 360 288 600 222 V343 H0 Z" fill="var(--leaf-light)"/>
      <path d="M0 230 C150 320 380 320 600 270 V343 H0 Z" fill="var(--leaf)"/>
    </svg>

    <div class="brand">
      <span class="brand-dot"></span>
      <span class="brand-name">Verdant Terraces</span>
    </div>
  </section>

</main>
</body>
</html>
```